I would like to modify/update my 2 step login screen

I want a more modern looking login page for our document imaging application. I need to keep all of the same elements and buttons that currently exist. The first 2 screens are the login. The 3rd is a screenshot of the actual application home page.

```html
<!DOCTYPE html>
<html lang="en">
<head>
<meta charset="utf-8">
<title>Login to MDDS – screen states</title>
<link href="https://fonts.googleapis.com/css2?family=Inter:wght@400;500;600;700&display=swap" rel="stylesheet">
<style>
  :root{
    --canvas:#f0f0f0;
    --screen:#fafafa;
    --header:#3a3a3c;
    --header-text:#ffffff;
    --header-muted:#9a9a9c;
    --card:#fafafa;
    --line:#e2e2e2;
    --field-line:#d6d6d6;
    --text:#2b2b2b;
    --muted:#9b9b9b;
    --green:#5cb85c;
    --green-link:#4caf50;
    --red:#e5484d;
    --disabled:#c9c9c9;
  }
  *{box-sizing:border-box;margin:0;padding:0}
  html,body{width:1200px;height:482px;overflow:hidden;background:var(--canvas)}
  body{position:relative;font-family:"Inter",Arial,sans-serif;color:var(--text)}

  .screen{position:absolute;width:371px;height:209px;background:var(--screen);overflow:hidden}
  .col-1{left:21.4px}.col-2{left:414.6px}.col-3{left:807.4px}
  .row-1{top:21.9px}.row-2{top:252px}

  .site-header{position:absolute;left:0;top:0;width:100%;height:26px;background:var(--header)}
  .brand{position:absolute;left:9.3px;top:8px;display:flex;align-items:center;gap:2.5px;
    color:var(--header-text);font-size:5px;font-weight:700;letter-spacing:.1px}
  .brand-dot{width:7px;height:7px;border-radius:50%;background:var(--header-text)}
  .site-nav{position:absolute;right:8.4px;top:8px;text-align:right;font-size:3.1px;line-height:6px}
  .site-nav .links{color:var(--header-text);font-weight:500}
  .site-nav .links span{margin:0 1.6px;color:var(--header-muted)}
  .site-nav .copyright{color:var(--header-muted)}

  .card{position:absolute;left:98.8px;top:43.3px;width:173.8px;height:66px;background:var(--card);
    border:0.5px solid var(--line);border-radius:2px}
  .card.tall{top:43.8px;height:119.2px}
  .card-title{position:absolute;left:6.5px;top:5px;font-size:6.4px;font-weight:600;line-height:7.5px}
  .card-error{position:absolute;right:6.5px;top:6.8px;font-size:3.6px;color:var(--red)}
  .card-rule{position:absolute;left:0;right:0;top:17.3px;border-top:0.5px solid var(--line)}

  .field{position:absolute;left:21.9px;width:130.5px;height:11.2px;border:0.5px solid var(--field-line);
    border-radius:1.5px;background:#fff;display:flex;align-items:center;padding:0 3px;gap:3px;font-size:3.7px}
  .field.active{border-color:var(--green)}
  .field.error{border-color:var(--red)}
  .field .value{flex:1;white-space:nowrap}
  .field .placeholder{flex:1;color:var(--muted)}
  .field .dots{flex:1;font-size:4.6px;letter-spacing:.3px}
  .field svg{width:5px;height:5px;flex:none}
  .caret{display:inline-block;width:0.4px;height:5px;background:var(--text);vertical-align:middle;margin-left:.3px}
  .f-db{top:26.6px}.f-user{top:41.5px}.f-pass{top:56.9px}

  .btn{position:absolute;right:21.4px;height:10.3px;border-radius:1.5px;color:#fff;font-size:3.6px;
    font-weight:600;display:flex;align-items:center;justify-content:center;letter-spacing:.2px}
  .btn.primary{background:var(--green)}
  .btn.off{background:var(--disabled)}
  .btn-next{top:47.1px;width:23.3px}
  .btn-login{top:77.4px;width:25.2px}

  .back-row{position:absolute;left:21.9px;top:26.4px;display:flex;align-items:center;font-size:3.6px}
  .back-row .back{width:5px;height:5px}
  .back-row .sep{width:.5px;height:6px;background:var(--line);margin:0 5px}
  .back-row .db{width:5px;height:5px;margin-right:2px}
  .back-row b{font-weight:600;margin-left:1px}

  .forgot{position:absolute;left:21.9px;top:80.6px;font-size:3.6px;color:var(--green-link);font-weight:500}
  .alt-divider{position:absolute;left:21.9px;width:130.5px;top:96.5px;border-top:0.5px solid var(--line)}
  .alt-divider span{position:absolute;left:50%;top:-2px;transform:translateX(-50%);background:var(--card);
    padding:0 3px;font-size:2.9px;color:var(--muted);letter-spacing:.1px;white-space:nowrap}
  .provider{position:absolute;top:105.3px;width:5.6px;height:5.6px;border-radius:50%;background:#bdbdbd}
  .p1{left:56.8px}.p2{left:84.3px}.p3{left:111.4px}

  .notice{position:absolute;left:0;width:100%;text-align:center;font-size:3.6px;line-height:6px;color:var(--text)}
  .notice b{font-weight:600}
  .row-1 .notice{top:115.8px}
  .row-2 .notice{top:170px}
</style>
</head>
<body>

<svg width="0" height="0" style="position:absolute">
  <defs>
    <symbol id="i-db" viewBox="0 0 10 10"><rect x="1" y="1.5" width="8" height="3" rx=".8" fill="none" stroke="#555" stroke-width=".8"/><rect x="1" y="5.5" width="8" height="3" rx=".8" fill="none" stroke="#555" stroke-width=".8"/></symbol>
    <symbol id="i-user" viewBox="0 0 10 10"><circle cx="5" cy="3.4" r="2" fill="none" stroke="#555" stroke-width=".8"/><path d="M1.5 9c.4-2 1.8-3 3.5-3s3.1 1 3.5 3" fill="none" stroke="#555" stroke-width=".8"/></symbol>
    <symbol id="i-lock" viewBox="0 0 10 10"><rect x="2" y="4.5" width="6" height="4.5" rx=".8" fill="none" stroke="#555" stroke-width=".8"/><path d="M3.3 4.5V3a1.7 1.7 0 0 1 3.4 0v1.5" fill="none" stroke="#555" stroke-width=".8"/></symbol>
    <symbol id="i-eye" viewBox="0 0 10 10"><path d="M1 5s1.5-3 4-3 4 3 4 3-1.5 3-4 3-4-3-4-3z" fill="none" stroke="#888" stroke-width=".7"/><circle cx="5" cy="5" r="1.2" fill="none" stroke="#888" stroke-width=".7"/><path d="M1.8 8.5l6.4-7" stroke="#888" stroke-width=".7"/></symbol>
    <symbol id="i-clear" viewBox="0 0 10 10"><circle cx="5" cy="5" r="3.8" fill="none" stroke="#888" stroke-width=".7"/><path d="M3.6 3.6l2.8 2.8M6.4 3.6L3.6 6.4" stroke="#888" stroke-width=".7"/></symbol>
    <symbol id="i-back" viewBox="0 0 10 10"><path d="M8.5 5h-7M4 2.5L1.5 5 4 7.5" fill="none" stroke="#888" stroke-width=".7"/></symbol>
  </defs>
</svg>

<!-- Step 1: empty -->
<section class="screen col-1 row-1">
  <header class="site-header">
    <div class="brand"><span class="brand-dot"></span>Meridian Docs</div>
    <nav class="site-nav"><div class="links">Privacy<span>•</span>Remote Support<span>•</span>Contact Us</div><div class="copyright">Copyright 2007-2024 Meridian Docs</div></nav>
  </header>
  <div class="card">
    <h1 class="card-title">Login to MDDS</h1><div class="card-rule"></div>
    <div class="field f-db"><svg><use href="#i-db"/></svg><span class="placeholder">Database</span></div>
    <div class="btn off btn-next">NEXT</div>
  </div>
  <p class="notice">All activity on this site is being recorded.<br>Your IP Address is being saved as '<b>192.168.168.134</b>'.</p>
</section>

<!-- Step 1: typing -->
<section class="screen col-2 row-1">
  <header class="site-header">
    <div class="brand"><span class="brand-dot"></span>Meridian Docs</div>
    <nav class="site-nav"><div class="links">Privacy<span>•</span>Remote Support<span>•</span>Contact Us</div><div class="copyright">Copyright 2007-2024 Meridian Docs</div></nav>
  </header>
  <div class="card">
    <h1 class="card-title">Login to MDDS</h1><div class="card-rule"></div>
    <div class="field f-db active"><svg><use href="#i-db"/></svg><span class="value">ABC12345<i class="caret"></i></span><svg><use href="#i-clear"/></svg></div>
    <div class="btn primary btn-next">NEXT</div>
  </div>
  <p class="notice">All activity on this site is being recorded.<br>Your IP Address is being saved as '<b>192.168.168.134</b>'.</p>
</section>

<!-- Step 1: error -->
<section class="screen col-3 row-1">
  <header class="site-header">
    <div class="brand"><span class="brand-dot"></span>Meridian Docs</div>
    <nav class="site-nav"><div class="links">Privacy<span>•</span>Remote Support<span>•</span>Contact Us</div><div class="copyright">Copyright 2007-2024 Meridian Docs</div></nav>
  </header>
  <div class="card">
    <h1 class="card-title">Login to MDDS</h1><span class="card-error">Invalid database.</span><div class="card-rule"></div>
    <div class="field f-db error"><svg><use href="#i-db"/></svg><span class="value">ABC12345XYZ</span><svg><use href="#i-clear"/></svg></div>
    <div class="btn primary btn-next">NEXT</div>
  </div>
  <p class="notice">All activity on this site is being recorded.<br>Your IP Address is being saved as '<b>192.168.168.134</b>'.</p>
</section>

<!-- Step 2: empty -->
<section class="screen col-1 row-2">
  <header class="site-header">
    <div class="brand"><span class="brand-dot"></span>Meridian Docs</div>
    <nav class="site-nav"><div class="links">Privacy<span>•</span>Remote Support<span>•</span>Contact Us</div><div class="copyright">Copyright 2007-2024 Meridian Docs</div></nav>
  </header>
  <div class="card tall">
    <h1 class="card-title">Login to MDDS</h1><div class="card-rule"></div>
    <div class="back-row"><svg class="back"><use href="#i-back"/></svg><i class="sep"></i><svg class="db"><use href="#i-db"/></svg>Database: <b>ABC12345</b></div>
    <div class="field f-user"><svg><use href="#i-user"/></svg><span class="placeholder">Username</span></div>
    <div class="field f-pass"><svg><use href="#i-lock"/></svg><span class="placeholder">Password</span><svg><use href="#i-eye"/></svg></div>
    <span class="forgot">Forgot Password?</span>
    <div class="btn off btn-login">LOGIN</div>
    <div class="alt-divider"><span>OR LOGIN WITH</span></div>
    <i class="provider p1"></i><i class="provider p2"></i><i class="provider p3"></i>
  </div>
  <p class="notice">All activity on this site is being recorded.<br>Your IP Address is being saved as '<b>192.168.168.134</b>'.</p>
</section>

<!-- Step 2: typing -->
<section class="screen col-2 row-2">
  <header class="site-header">
    <div class="brand"><span class="brand-dot"></span>Meridian Docs</div>
    <nav class="site-nav"><div class="links">Privacy<span>•</span>Remote Support<span>•</span>Contact Us</div><div class="copyright">Copyright 2007-2024 Meridian Docs</div></nav>
  </header>
  <div class="card tall">
    <h1 class="card-title">Login to MDDS</h1><div class="card-rule"></div>
    <div class="back-row"><svg class="back"><use href="#i-back"/></svg><i class="sep"></i><svg class="db"><use href="#i-db"/></svg>Database: <b>ABC12345</b></div>
    <div class="field f-user"><svg><use href="#i-user"/></svg><span class="value">JohnDoe123</span><svg><use href="#i-clear"/></svg></div>
    <div class="field f-pass active"><svg><use href="#i-lock"/></svg><span class="dots">●●●<i class="caret"></i></span><svg><use href="#i-eye"/></svg><svg><use href="#i-clear"/></svg></div>
    <span class="forgot">Forgot Password?</span>
    <div class="btn primary btn-login">LOGIN</div>
    <div class="alt-divider"><span>OR LOGIN WITH</span></div>
    <i class="provider p1"></i><i class="provider p2"></i><i class="provider p3"></i>
  </div>
  <p class="notice">All activity on this site is being recorded.<br>Your IP Address is being saved as '<b>192.168.168.134</b>'.</p>
</section>

<!-- Step 2: error -->
<section class="screen col-3 row-2">
  <header class="site-header">
    <div class="brand"><span class="brand-dot"></span>Meridian Docs</div>
    <nav class="site-nav"><div class="links">Privacy<span>•</span>Remote Support<span>•</span>Contact Us</div><div class="copyright">Copyright 2007-2024 Meridian Docs</div></nav>
  </header>
  <div class="card tall">
    <h1 class="card-title">Login to MDDS</h1><span class="card-error">Invalid username and/or password.</span><div class="card-rule"></div>
    <div class="back-row"><svg class="back"><use href="#i-back"/></svg><i class="sep"></i><svg class="db"><use href="#i-db"/></svg>Database: <b>ABC12345</b></div>
    <div class="field f-user error"><svg><use href="#i-user"/></svg><span class="value">johndoe</span><svg><use href="#i-clear"/></svg></div>
    <div class="field f-pass error"><svg><use href="#i-lock"/></svg><span class="dots">●●●●●●</span><svg><use href="#i-eye"/></svg><svg><use href="#i-clear"/></svg></div>
    <span class="forgot">Forgot Password?</span>
    <div class="btn primary btn-login">LOGIN</div>
    <div class="alt-divider"><span>OR LOGIN WITH</span></div>
    <i class="provider p1"></i><i class="provider p2"></i><i class="provider p3"></i>
  </div>
  <p class="notice">All activity on this site is being recorded.<br>Your IP Address is being saved as '<b>192.168.168.134</b>'.</p>
</section>

</body>
</html>
```